Advertising Material for Event

We are needing some advertising material done for an event. It can all be roughly the same except the two social media posts. We need:
- A banner
- A flyer
- 2 X social media posts

I have attached some examples of what we have done in the past. I have also attached a word document with the information.

Our colours are:
NAVY BLUE: Hex = #041E42 // RGB = 4 / 30 / 66 // CMYK = 100 / 90 / 13 / 68 // Pantone = 289 C
LIME GREEN: Hex = #97D700 // RGB = 151 / 215 / 0 // CMYK = 46 / 0 / 90 / 0 // Pantone = 375 C
WHITE

Our font are:
Avenir next regular, bold and demi bold
Freshman

Colors

Designer to choose colors to be used in the design.

Requirements
Must have
• Include photos provided. All info provided
Nice to have
• not cluttered

```html
<!DOCTYPE html>
<html lang="en">
<head>
<meta charset="utf-8">
<title>2022 Cheerleading Team Placements</title>
<link href="https://fonts.googleapis.com/css2?family=Graduate&family=Nunito+Sans:wght@400;600;700;800;900&family=Oswald:wght@600;700&display=swap" rel="stylesheet">
<style>
:root{
  --navy:#041E42;
  --navy-deep:#021330;
  --lime:#97D700;
  --green:#4f9a12;
  --white:#ffffff;
  --ink:#1b1f2a;
  --sans:"Nunito Sans",sans-serif;
  --varsity:"Graduate",serif;
  --cond:"Oswald",sans-serif;
}
*{margin:0;padding:0;box-sizing:border-box}
html,body{width:1200px;height:1200px;overflow:hidden;background:var(--white)}
.poster{position:relative;width:1200px;height:1200px;overflow:hidden;font-family:var(--sans);color:var(--navy)}
.photo{position:absolute;inset:0;background:
  radial-gradient(ellipse at 85% 30%,rgba(255,255,255,.35),transparent 40%),
  linear-gradient(180deg,#5ea616 0%,#3f8a1e 35%,#0b2b52 62%,var(--navy-deep) 100%)}
.header{position:absolute;left:0;top:0;width:420px;height:194px;background:var(--navy);
  clip-path:polygon(0 0,402px 0,348px 194px,0 194px)}
.brand{position:absolute;left:0;top:0;width:360px;height:194px;display:flex;align-items:center;justify-content:center;gap:12px;
  color:var(--lime);font-weight:800;font-size:30px;letter-spacing:1px}
.brand-dot{width:22px;height:22px;border-radius:50%;background:var(--lime)}
.info{position:absolute;left:0;top:194px;width:860px;height:930px;background:var(--white);
  clip-path:polygon(0 0,397px 0,855px 930px,0 930px)}
.year{position:absolute;left:76px;top:214px;font-family:var(--varsity);font-size:132px;line-height:1;color:var(--navy);
  -webkit-text-stroke:3px #1a5fc4;letter-spacing:-2px}
.title-band{position:absolute;left:0;top:362px;width:706px;height:98px;
  background:linear-gradient(90deg,var(--navy) 60%,#000 100%);
  border-top:6px solid var(--lime);border-bottom:6px solid var(--lime);
  clip-path:polygon(0 0,660px 0,706px 98px,0 98px);display:flex;align-items:center}
.title{margin-left:76px;font-family:var(--varsity);font-size:60px;line-height:1;
  background:linear-gradient(180deg,#fff 0%,#d5d7da 55%,#8c9096 100%);-webkit-background-clip:text;background-clip:text;color:transparent;letter-spacing:1px}
.subtitle{position:absolute;left:84px;top:476px;font-size:40px;font-weight:800;color:var(--navy);letter-spacing:.5px}
.intro{position:absolute;left:93px;top:546px;width:470px;font-size:22px;font-weight:700;line-height:28px;color:var(--ink)}
.date{position:absolute;left:86px;top:672px;width:249px;height:108px;border:3px solid var(--navy);border-radius:8px;display:flex;overflow:hidden}
.date-day{width:132px;text-align:center;color:var(--ink);font-weight:700;font-size:18px;line-height:1.15;padding-top:6px}
.date-num{font-size:36px;font-weight:900;line-height:1.05}
.date-num sup{font-size:20px}
.date-year{flex:1;background:var(--navy);color:var(--lime);font-family:var(--cond);font-weight:600;font-size:48px;display:flex;align-items:center;justify-content:center}
.sessions{position:absolute;left:364px;top:672px;width:220px}
.session-label{font-size:16px;font-weight:800;color:var(--ink)}
.session-time{font-size:29px;font-weight:800;color:var(--navy);line-height:1.05}
.session+.session{border-top:2px dotted var(--navy);margin-top:6px;padding-top:6px}
.venue{position:absolute;left:0;top:796px;width:700px;height:58px;background:linear-gradient(90deg,var(--navy) 55%,#000 100%);
  border-top:4px solid var(--lime);border-bottom:4px solid var(--lime);clip-path:polygon(0 0,672px 0,700px 58px,0 58px);
  display:flex;align-items:center;color:var(--white);font-weight:700;font-size:20px}
.venue svg{margin:0 16px 0 78px}
.cost{position:absolute;left:84px;top:868px;display:flex;align-items:center}
.cost-label{font-family:var(--varsity);font-size:48px;color:var(--navy);margin-right:30px}
.cost-amount{font-family:var(--cond);font-weight:700;font-size:74px;line-height:1;color:#222;margin-right:8px}
.cost-note{font-size:30px;font-weight:700;line-height:32px;color:#222}
.tag{position:absolute;left:86px;top:972px;width:452px;height:36px;background:var(--lime);border:1px solid #5a8a00;
  clip-path:polygon(0 0,440px 0,452px 36px,0 36px);font-size:18px;font-weight:800;color:var(--navy);padding:6px 10px}
.more{position:absolute;left:86px;top:1016px;width:720px;color:var(--ink)}
.more h3{font-size:20px;font-weight:800}
.more p{font-size:15px;font-weight:700;line-height:20px;color:#333}
.footer{position:absolute;left:0;top:1124px;width:1200px;height:76px;background:var(--navy);display:flex;align-items:center;color:var(--white)}
.phone{display:flex;align-items:center;gap:14px;margin-left:84px;font-size:42px;font-weight:800}
.divider{width:1px;height:48px;background:#8a94a8;margin:0 38px 0 40px}
.contacts{font-size:21px;line-height:26px}
.contacts div{display:flex;align-items:center;gap:12px}
</style>
</head>
<body>
<div class="poster">
  <div class="photo" role="img" aria-label="Photo of a cheerleading squad performing a stunt with a flyer held high, sparkles and light trails on a green to navy backdrop"></div>
  <div class="header"></div>
  <div class="brand"><span class="brand-dot"></span>APEX GYMSPORTS</div>
  <div class="info"></div>

  <div class="year">2022</div>
  <div class="title-band"><span class="title">CHEERLEADING</span></div>
  <h2 class="subtitle">TEAM PLACEMENTS</h2>
  <p class="intro">Try out for a cheerleading team! Everyone is welcome and will be placed on a team, regardless of skill level.</p>

  <div class="date">
    <div class="date-day">SATURDAY<div class="date-num">11<sup>th</sup></div>DECEMBER</div>
    <div class="date-year">2021</div>
  </div>
  <div class="sessions">
    <div class="session"><div class="session-label">11 YEARS AND UNDER</div><div class="session-time">3:30 - 4:30pm</div></div>
    <div class="session"><div class="session-label">12 YEARS AND OVER</div><div class="session-time">4:45 - 5:45pm</div></div>
  </div>

  <div class="venue">
    <svg width="28" height="30" viewBox="0 0 28 30" aria-hidden="true"><path d="M14 2a8 8 0 0 0-8 8c0 6 8 13 8 13s8-7 8-13a8 8 0 0 0-8-8z" fill="#97D700"/><circle cx="14" cy="10" r="3" fill="#041E42"/><ellipse cx="14" cy="26" rx="11" ry="3" fill="none" stroke="#97D700" stroke-width="2"/></svg>
    Apex Gymsports, 14-16 Marlow Place Westbrook
  </div>

  <div class="cost">
    <span class="cost-label">COST:</span>
    <span class="cost-amount">$10</span>
    <span class="cost-note">and includes an Apex<br>merchandise pack</span>
  </div>

  <div class="tag">SEMI-COMPETITIVE TEAMS ALSO AVAILABLE</div>
  <div class="more">
    <h3>Unsure what cheerleading is like?</h3>
    <p>Come along to our open week to try it out with our current Apex cheerleading teams. Classes are available from the 6th-10th of December. Please contact us for more information!</p>
  </div>

  <footer class="footer">
    <div class="phone">
      <svg width="30" height="30" viewBox="0 0 24 24" aria-hidden="true"><path d="M6.6 10.8a15 15 0 0 0 6.6 6.6l2.2-2.2a1 1 0 0 1 1-.25 11 11 0 0 0 3.6.6 1 1 0 0 1 1 1V20a1 1 0 0 1-1 1A17 17 0 0 1 3 4a1 1 0 0 1 1-1h3.5a1 1 0 0 1 1 1c0 1.25.2 2.45.6 3.6a1 1 0 0 1-.25 1z" fill="#97D700"/></svg>
      95550123
    </div>
    <div class="divider"></div>
    <div class="contacts">
      <div><svg width="26" height="18" viewBox="0 0 26 18" aria-hidden="true"><rect x="1" y="1" width="24" height="16" fill="#97D700"/><path d="M1 1l12 9 12-9" fill="none" stroke="#041E42" stroke-width="2"/></svg>cheer@apexgymsports.com</div>
      <div><svg width="26" height="22" viewBox="0 0 24 24" aria-hidden="true"><circle cx="12" cy="12" r="10" fill="none" stroke="#97D700" stroke-width="2"/><path d="M2 12h20M12 2c3 3 3 17 0 20M12 2c-3 3-3 17 0 20" fill="none" stroke="#97D700" stroke-width="2"/></svg>www.apexgymsports.com</div>
    </div>
  </footer>
</div>
</body>
</html>
```